Merry Meadow Roasters

We need a website to sell coffee with a horse theme. We already have a logo and have designed 4 different coffee bags/flavors so far, each of which will be available in ground or whole bean. The brand is intended to be light hearted/whimsical.

Requirements
Must have
• incorporation of attached photos
Nice to have
• underlying background theme with sky/grass

```html
<!DOCTYPE html>
<html lang="en">
<head>
<meta charset="utf-8">
<title>Merry Meadow Roasters</title>
<link href="https://fonts.googleapis.com/css2?family=Federo&family=Roboto:wght@400;500;700&family=PT+Serif&display=swap" rel="stylesheet">
<style>
:root{
  --orange:#d4935a;
  --orange-dark:#c7834a;
  --brown:#2a1a10;
  --cream:#fbf0e8;
  --ink:#1e1e1e;
  --muted:#5a5a5a;
  --white:#ffffff;
}
*{box-sizing:border-box;margin:0;padding:0}
html,body{width:1200px;height:4132px;overflow:hidden}
body{position:relative;background:var(--white);font-family:"Roboto",Arial,sans-serif;color:var(--ink)}
.abs{position:absolute}
.display{font-family:"Federo",sans-serif;font-weight:400}
.btn{position:absolute;display:flex;align-items:center;justify-content:center;border-radius:20px;background:var(--orange);color:var(--white);font-size:12px;font-weight:700;letter-spacing:.3px;text-transform:uppercase}
.rule{position:absolute;height:3px;width:80px;background:var(--orange);border-radius:2px}
.para{position:absolute;font-size:14.3px;line-height:24px;color:var(--muted);text-align:justify}

/* header */
.site-header{position:absolute;left:100px;top:0;width:1000px;height:80px;background:var(--white);border-radius:0 0 22px 22px;z-index:3}
.brand{position:absolute;left:143px;top:0;width:112px;height:109px;background:var(--white);z-index:4;display:flex;align-items:center;justify-content:center;text-align:center;font-family:"Roboto",sans-serif;font-weight:500;font-size:14px;line-height:17px;color:var(--brown)}
.nav{position:absolute;top:36px;font-size:14px;font-weight:500;color:var(--ink);z-index:4}
.nav.active{color:var(--orange)}
.nav.active::after{content:"";position:absolute;left:-4px;right:-4px;bottom:-10px;height:2px;background:var(--orange)}

/* hero */
.hero-title{position:absolute;left:144px;top:218px;font-size:62px;line-height:64px;color:var(--white)}
.hero-arrow{position:absolute;top:470px;width:48px;height:48px;border-radius:50%;display:flex;align-items:center;justify-content:center}

/* about */
.photo{position:absolute}

/* products */
.products{position:absolute;left:0;top:1304px;width:1200px;height:602px;background:var(--cream)}
.section-title{position:absolute;left:0;width:1200px;text-align:center;font-size:44px;color:var(--ink)}
.product-card{position:absolute;top:237px;width:210px;height:211px;border-radius:40px;background:var(--orange)}
.bag{position:absolute;left:52px;top:22px;width:106px;height:162px;background:linear-gradient(180deg,#d9c3a3,#b99a73 70%,#3a2a20 72%,#3a2a20);border-radius:3px}
.product-label{position:absolute;left:20px;top:185px;width:170px;height:71px;background:var(--white);border-radius:6px;text-align:center;box-shadow:0 4px 12px rgba(0,0,0,.08)}
.product-label .name{margin-top:16px;font-size:15px;font-weight:500;color:var(--ink)}
.product-label .price{margin-top:10px;font-size:15px;font-weight:700;color:var(--orange)}
.product-label.dark{background:var(--brown);height:103px}
.product-label.dark .name,.product-label.dark .price{color:var(--white)}
.product-label .buy{margin-top:12px;font-size:12px;font-weight:700;color:var(--white);text-decoration:underline}
.badge{position:absolute;left:544px;top:1532px;width:42px;height:42px;border-radius:50%;background:var(--brown);color:var(--white);font-size:9px;font-weight:700;display:flex;align-items:center;justify-content:center}

/* menu */
.menu-card{position:absolute;width:438px;height:146px;border-radius:73px;background:var(--white);box-shadow:0 6px 20px rgba(0,0,0,.09)}
.menu-img{position:absolute;left:8px;top:13px;width:134px;height:120px;border-radius:60px 40px 60px 40px}
.menu-card h3{position:absolute;left:162px;top:29px;font-size:19px;font-weight:500;color:var(--ink)}
.menu-card p{position:absolute;left:162px;top:64px;width:240px;font-size:13px;line-height:20px;color:var(--muted)}

/* accessories */
.accessories{position:absolute;left:0;top:2568px;width:1200px;height:361px;background:linear-gradient(135deg,#d7995f,#c98a52 50%,#dba26a)}
.accessories h2{position:absolute;left:0;width:1200px;top:78px;text-align:center;font-size:44px;line-height:49px;color:var(--white);letter-spacing:1px}

/* footer */
.footer-head{position:absolute;top:3800px;font-family:"PT Serif",serif;font-size:18px;color:var(--white)}
.footer-list{position:absolute;top:3841px;list-style:none;font-size:14px;color:var(--white)}
.footer-list li{height:24px;display:flex;align-items:center}
.footer-list li::before{content:"";width:8px;height:8px;border-radius:50%;background:var(--orange);margin-right:16px}
.contact-item{position:absolute;left:585px;font-size:14px;line-height:22px;color:var(--white)}
.contact-item b{font-weight:700}
.contact-item svg{position:absolute;left:0;top:4px}
.contact-item .txt{padding-left:24px}
.social{position:absolute;top:3959px;width:34px;height:34px;border-radius:50%;border:1.5px solid var(--white)}
</style>
</head>
<body>

<!-- hero -->
<svg class="abs" style="left:0;top:0" width="1200" height="720" viewBox="0 0 1200 720">
  <defs>
    <linearGradient id="heroTone" x1="0" y1="0" x2="1" y2="0.4">
      <stop offset="0" stop-color="#0f0b08"/>
      <stop offset="0.4" stop-color="#3b2a1c"/>
      <stop offset="0.65" stop-color="#8a5a2a"/>
      <stop offset="1" stop-color="#4a4a4e"/>
    </linearGradient>
  </defs>
  <path d="M0,605 C140,585 250,690 380,610 C470,550 520,600 600,680 C680,745 760,655 860,620 C980,585 1080,675 1200,695 L1200,560 L0,560Z" fill="var(--orange)"/>
  <path role="img" aria-label="Photo of two friends laughing over cups of coffee in a cafe" d="M0,560 C140,540 250,640 380,560 C470,500 520,550 600,630 C680,695 760,605 860,570 C980,535 1080,625 1200,645 L1200,0 L0,0Z" fill="url(#heroTone)"/>
</svg>

<header class="site-header"></header>
<div class="brand">Merry Meadow<br>Roasters</div>
<span class="nav active" style="left:383px">Home</span>
<span class="nav" style="left:450px">About</span>
<span class="nav" style="left:517px">Products</span>
<span class="nav" style="left:604px">Menus</span>
<span class="nav" style="left:677px">Accessories</span>
<span class="nav" style="left:785px">Contact</span>
<div class="btn" style="left:908px;top:22px;width:148px;height:39px;z-index:4">Get a Quote</div>

<h1 class="hero-title display">Merry Meadow<br>Roasters</h1>
<div class="btn" style="left:144px;top:359px;width:146px;height:37px">Get Started</div>
<div class="hero-arrow" style="left:143px;background:var(--white)">
  <svg width="14" height="14" viewBox="0 0 14 14"><path d="M9 2 L4 7 L9 12" fill="none" stroke="#333" stroke-width="1.8"/></svg>
</div>
<div class="hero-arrow" style="left:199px;background:var(--orange)">
  <svg width="14" height="14" viewBox="0 0 14 14"><path d="M5 2 L10 7 L5 12" fill="none" stroke="#fff" stroke-width="1.8"/></svg>
</div>

<!-- about -->
<div class="photo" role="img" aria-label="Photo of a smiling woman holding a coffee cup" style="left:144px;top:791px;width:230px;height:231px;border-radius:34px;background:linear-gradient(135deg,#5a3a28,#a4623c 60%,#d8c3a8)"></div>
<div class="photo" role="img" aria-label="Photo of a latte with heart art" style="left:399px;top:829px;width:159px;height:159px;border-radius:50%;background:radial-gradient(circle at 45% 45%,#f1dcc0,#c58a52 45%,#6a4a35 75%)"></div>
<div class="photo" role="img" aria-label="Photo of a young woman holding a mug" style="left:234px;top:1046px;width:113px;height:114px;border-radius:50%;background:radial-gradient(circle,#8a5a3a,#c47a46 55%,#e8d8c8)"></div>
<div class="photo" role="img" aria-label="Photo of an older woman smiling with a cup" style="left:383px;top:1009px;width:188px;height:188px;border-radius:30px;background:linear-gradient(135deg,#d8d8d4,#8a9a7a 60%,#6e8a62)"></div>

<h2 class="abs display" style="left:627px;top:805px;font-size:44px">About Us</h2>
<div class="rule" style="left:627px;top:865px"></div>
<p class="para" style="left:627px;top:885px;width:427px">Lorem ipsum dolor sit amet, consectetur adipiscing elit, sed do eiusmod tempor incididunt ut labore et dolore magna aliqua. Ut enim ad minim veniam, quis nostrud exercitation ullamco laboris nisi ut aliquip ex ea commodo consequat. Duis aute irure dolor in reprehenderit in voluptate velit esse cillum dolore eu fugiat nulla pariatur. Excepteur sint oc=caecat cupidatat non proident, sunt in culpa qui officia deserunt mollit anim id est laborum. Lorem ipsum dolor sit amet, consectetur adipiscing elit, sed do eiusmod tempor incididunt ut labore et dolore magna aliqua. Lorem ipsum dolor sit amet, consectetur adipiscing elit, sed do eiusmod tempor incididunt ut labore et dolore magna aliqua.</p>
<div class="btn" style="left:627px;top:1168px;width:148px;height:37px">Learn More</div>

<!-- products -->
<section class="products">
  <h2 class="section-title display" style="top:70px">Featured Products</h2>
  <p class="abs" style="left:300px;top:170px;width:600px;text-align:center;font-size:14.3px;line-height:24px;color:var(--muted)">Lorem ipsum dolor sit amet, consectetur adipiscing elit, sed do eiusmod tempor incididunt ut labore et dolore magna aliqua.</p>

  <svg class="abs" style="left:62px;top:352px" width="20" height="26" viewBox="0 0 20 26"><path d="M14 3 L5 13 L14 23" fill="none" stroke="#222" stroke-width="2.4"/></svg>
  <svg class="abs" style="left:1118px;top:352px" width="20" height="26" viewBox="0 0 20 26"><path d="M6 3 L15 13 L6 23" fill="none" stroke="#222" stroke-width="2.4"/></svg>

  <div class="product-card" style="left:144px">
    <div class="bag" role="img" aria-label="Coffee bag, blend one"></div>
    <div class="product-label"><div class="name">Lorem ipsum dolor</div><div class="price">$25.00</div></div>
  </div>
  <div class="product-card" style="left:377px">
    <div class="bag" role="img" aria-label="Coffee bag, blend two"></div>
    <div class="product-label dark"><div class="name">Lorem ipsum dolor</div><div class="price">$25.00</div><div class="buy">BUY NOW</div></div>
  </div>
  <div class="product-card" style="left:611px">
    <div class="bag" role="img" aria-label="Coffee bag, blend three"></div>
    <div class="product-label"><div class="name">Lorem ipsum dolor</div><div class="price">$25.00</div></div>
  </div>
  <div class="product-card" style="left:844px">
    <div class="bag" role="img" aria-label="Coffee bag, blend four"></div>
    <div class="product-label"><div class="name">Lorem ipsum dolor</div><div class="price">$25.00</div></div>
  </div>
</section>
<div class="badge">NEW</div>

<!-- menu -->
<h2 class="section-title display" style="top:1975px">Coffee Menu</h2>
<div class="rule" style="left:560px;top:2047px"></div>

<div class="menu-card" style="left:144px;top:2079px">
  <div class="menu-img" role="img" aria-label="Photo of a cappuccino with coffee beans" style="background:linear-gradient(135deg,#f2ece6,#b9a38d 55%,#4a2e1e)"></div>
  <h3>Lorem ipsum dolor</h3>
  <p>Lorem ipsum dolor sit amet, consect etur adipiscing elit, sed do eiusmod tempor incididunt</p>
</div>
<div class="menu-card" style="left:616px;top:2079px">
  <div class="menu-img" role="img" aria-label="Photo of espresso surrounded by beans" style="background:linear-gradient(135deg,#5a3220,#b68a64 50%,#3a2216)"></div>
  <h3>Lorem ipsum dolor</h3>
  <p>Lorem ipsum dolor sit amet, consect etur adipiscing elit, sed do eiusmod tempor incididunt</p>
</div>
<div class="menu-card" style="left:144px;top:2247px">
  <div class="menu-img" role="img" aria-label="Photo of latte art on a wooden table" style="background:linear-gradient(135deg,#7a4a2a,#c99a6e 55%,#3a2416)"></div>
  <h3>Lorem ipsum dolor</h3>
  <p>Lorem ipsum dolor sit amet, consect etur adipiscing elit, sed do eiusmod tempor incididunt</p>
</div>
<div class="menu-card" style="left:616px;top:2247px">
  <div class="menu-img" role="img" aria-label="Photo of black coffee with scattered beans" style="background:linear-gradient(135deg,#e8e2dc,#6a4430 55%,#2a1810)"></div>
  <h3>Lorem ipsum dolor</h3>
  <p>Lorem ipsum dolor sit amet, consect etur adipiscing elit, sed do eiusmod tempor incididunt</p>
</div>
<div class="btn" style="left:513px;top:2425px;width:174px;height:37px">View More Menus</div>

<!-- accessories -->
<section class="accessories" role="img" aria-label="Warm toned photo of coffee brewing accessories and cups">
  <h2 class="display">Must Have Coffee Accessories<br>For Coffee Lovers</h2>
  <div class="rule" style="left:560px;top:197px;background:var(--white)"></div>
  <div class="btn" style="left:494px;top:223px;width:212px;height:39px;background:var(--white);color:var(--ink)">View Accessories</div>
</section>

<!-- sustainability -->
<h2 class="abs display" style="left:143px;top:3022px;font-size:43px;line-height:48px">Sustainability<br>and Community<br>Engagements</h2>
<div class="rule" style="left:143px;top:3178px"></div>
<p class="para" style="left:144px;top:3203px;width:426px">Lorem ipsum dolor sit amet, consectetur adipiscing elit, sed do eiusmod tempor incididunt ut labore et dolore magna aliqua. Ut enim ad minim veniam, quis nostrud exercitation ullamco laboris nisi ut aliquip ex ea commodo consequat. Duis aute irure dolor in reprehenderit in voluptate velit esse cillum dolore eu fugiat nulla pariatur. Excepteur sint oc=caecat cupidatat non proident, sunt in culpa qui officia deserunt mollit anim id est laborum. Lorem ipsum dolor sit amet, consectetur adipiscing elit, sed do eiusmod tempor incididunt ut labore et dolore magna aliqua.</p>
<div class="btn" style="left:144px;top:3434px;width:148px;height:39px">Learn More</div>
<div class="abs" style="left:884px;top:3367px;width:140px;height:140px;border-radius:50%;background:var(--orange)"></div>
<div class="abs" role="img" aria-label="Photo of a smiling woman in glasses holding a coffee cup" style="left:600px;top:3025px;width:452px;height:452px;border-radius:50%;background:radial-gradient(circle at 50% 40%,#c98a5e,#8a4a2c 55%,#4a3a32)"></div>

<!-- footer -->
<svg class="abs" style="left:0;top:3560px" width="1200" height="572" viewBox="0 0 1200 572">
  <path d="M0,60 C90,20 160,50 250,70 C330,85 380,10 470,5 C560,0 640,80 720,100 C820,125 860,50 960,45 C1060,40 1120,100 1200,110 L1200,572 L0,572Z" fill="var(--orange)"/>
  <path d="M0,95 C90,55 160,85 250,105 C330,120 380,45 470,40 C560,35 640,115 720,135 C820,160 860,85 960,80 C1060,75 1120,135 1200,145 L1200,572 L0,572Z" fill="var(--brown)"/>
</svg>

<div class="abs" style="left:143px;top:3810px;width:111px;height:112px;background:var(--white);display:flex;align-items:center;justify-content:center;text-align:center;font-size:14px;font-weight:500;line-height:17px;color:var(--brown)">Merry Meadow<br>Roasters</div>
<div class="social" style="left:143px"></div>
<div class="social" style="left:183px;background:var(--orange)"></div>
<div class="social" style="left:224px"></div>

<h4 class="footer-head" style="left:361px">QUICK LINKS</h4>
<ul class="footer-list" style="left:361px">
  <li>Home</li><li>About us</li><li>Products</li><li>Menus</li><li>Coffee Accessories</li><li>Blog</li><li>Contact us</li>
</ul>

<h4 class="footer-head" style="left:585px">CONTACT US</h4>
<div class="contact-item" style="top:3841px">
  <svg width="12" height="14" viewBox="0 0 12 14"><path d="M6 0 C2.7 0 0 2.6 0 5.8 C0 10 6 14 6 14 C6 14 12 10 12 5.8 C12 2.6 9.3 0 6 0Z M6 8 A2.2 2.2 0 1 1 6 3.6 A2.2 2.2 0 1 1 6 8Z" fill="var(--orange)"/></svg>
  <div class="txt"><b>Address :</b><br>12, Lorem ipsum dolor</div>
</div>
<div class="contact-item" style="top:3913px">
  <svg width="13" height="13" viewBox="0 0 13 13"><path d="M2.6 0.5 L4.8 3.2 L3.6 4.8 C4.4 6.4 6.6 8.6 8.2 9.4 L9.8 8.2 L12.5 10.4 L11 12.5 C6 12.5 0.5 7 0.5 2Z" fill="var(--orange)"/></svg>
  <div class="txt"><b>Phone :</b><br>+1 888 888 8888</div>
</div>
<div class="contact-item" style="top:3985px">
  <svg width="13" height="11" viewBox="0 0 13 11"><rect x="0" y="0.5" width="13" height="10" rx="1" fill="var(--orange)"/><path d="M0.5 1 L6.5 6 L12.5 1" fill="none" stroke="var(--brown)" stroke-width="1.2"/></svg>
  <div class="txt"><b>Email Address :</b><br>info@merrymeadow.com</div>
</div>

<h4 class="footer-head" style="left:815px">OUR NEWSLETTER</h4>
<div class="abs" style="left:815px;top:3842px;width:244px;height:37px;border-radius:19px;background:#3d2b1e;display:flex;align-items:center;padding-left:16px;font-size:14px;color:var(--white)">
  <svg width="14" height="11" viewBox="0 0 14 11" style="margin-right:10px"><rect width="14" height="11" rx="1" fill="var(--white)"/><path d="M0.5 1 L7 6 L13.5 1" fill="none" stroke="#3d2b1e" stroke-width="1.2"/></svg>Email address
</div>
<div class="btn" style="left:815px;top:3890px;width:124px;height:37px">Subscribe</div>

<p class="abs" style="left:0;top:4089px;width:1200px;text-align:center;font-size:13px;color:var(--white)">© Copyrights 2025 | All Rights Reserved</p>

</body>
</html>
```